KORV PTY LTD - Business Cards

Design a modern business card - using the attached Designs.
Same design as on the front, apart from the names/numbers/emails to be different.
We want the cards to be very glossy to stand out, do I think the simple black/white/metallic will be effective.
Both lots of details below:

Tom Wrenshaw
Director
tom_korv@nulvane.com
0438 274 093

Lewis Corbyn
Director
lewis_korv@nulvane.com
0419 385 642

Industry/Entity Type

Business

```html
<!DOCTYPE html>
<html lang="en">
<head>
<meta charset="utf-8">
<title>KORV PTY LTD – Business Cards</title>
<link href="https://fonts.googleapis.com/css2?family=Bitter:wght@400;700&display=swap" rel="stylesheet">
<style>
  :root {
    --stage: #e9e7e4;
    --card-white: #ffffff;
    --charcoal: #2a3136;
    --band-grey: #b9bdbc;
    --text-light: #ffffff;
    --mark-dark: #2f3437;
    --silver-1: #d9d9db;
    --silver-2: #f4f4f5;
    --silver-3: #a9a8ad;
    --silver-4: #8f8e94;
  }
  * { box-sizing: border-box; margin: 0; padding: 0; }
  html, body { width: 1200px; height: 475px; overflow: hidden; }
  body {
    background: var(--stage);
    font-family: "Bitter", Georgia, serif;
    position: relative;
  }
  .card {
    position: absolute;
    top: 62px;
    width: 540px;
    height: 350px;
    box-shadow: 0 6px 18px rgba(0,0,0,0.25);
    overflow: hidden;
  }
  .card--front { left: 40px; background: var(--card-white); }
  .card--back {
    left: 620px;
    background: linear-gradient(90deg, var(--silver-1) 0%, var(--silver-2) 18%, var(--silver-3) 40%, var(--silver-2) 62%, var(--silver-4) 85%, var(--silver-1) 100%);
  }
  .card__curves { position: absolute; inset: 0; }
  .brand {
    position: absolute;
    display: flex;
    align-items: center;
    gap: 12px;
    color: var(--mark-dark);
    font-weight: 700;
    letter-spacing: 0.06em;
    white-space: nowrap;
  }
  .brand__dot {
    border-radius: 50%;
    background: var(--mark-dark);
    flex: none;
  }
  .card--front .brand { left: 50%; top: 78px; transform: translateX(-50%); font-size: 30px; }
  .card--front .brand__dot { width: 34px; height: 34px; }
  .card--back .brand { left: 50%; top: 50%; transform: translate(-50%, -50%); font-size: 40px; }
  .card--back .brand__dot { width: 46px; height: 46px; }
  .contact {
    position: absolute;
    left: 0; right: 0;
    top: 232px;
    text-align: center;
    color: var(--text-light);
  }
  .contact__name { font-size: 19px; font-weight: 700; }
  .contact__role { font-weight: 400; font-size: 16px; }
  .contact__line {
    margin-top: 10px;
    font-size: 15px;
    display: flex;
    justify-content: center;
    align-items: center;
    gap: 7px;
  }
  .contact__line svg { width: 13px; height: 13px; fill: var(--text-light); }
</style>
</head>
<body>
  <section class="card card--front" aria-label="Card front">
    <svg class="card__curves" viewBox="0 0 540 350" preserveAspectRatio="none" aria-hidden="true">
      <path d="M0 212 Q280 262 540 95 L540 350 L0 350 Z" fill="var(--band-grey)"/>
      <path d="M0 222 Q280 272 540 108 L540 350 L0 350 Z" fill="var(--card-white)"/>
      <path d="M0 230 Q280 282 540 118 L540 350 L0 350 Z" fill="var(--charcoal)"/>
    </svg>
    <div class="brand"><span class="brand__dot"></span>KORV PTY LTD</div>
    <div class="contact">
      <p class="contact__name">Lewis Corbyn,<span class="contact__role"> Director</span></p>
      <p class="contact__line">
        <svg viewBox="0 0 24 24" aria-hidden="true"><path d="M6.6 10.8a15.1 15.1 0 0 0 6.6 6.6l2.2-2.2a1 1 0 0 1 1-.25 11.4 11.4 0 0 0 3.6.57 1 1 0 0 1 1 1V20a1 1 0 0 1-1 1A17 17 0 0 1 3 4a1 1 0 0 1 1-1h3.5a1 1 0 0 1 1 1c0 1.25.2 2.45.57 3.57a1 1 0 0 1-.25 1z"/></svg>
        0419 385 642
      </p>
      <p class="contact__line">
        <svg viewBox="0 0 24 24" aria-hidden="true"><path d="M2 5h20v14H2z M2 5l10 8 10-8" fill="none" stroke="#fff" stroke-width="2"/></svg>
        lewis_korv@nulvane.com
      </p>
    </div>
  </section>

  <section class="card card--back" aria-label="Card back">
    <div class="brand"><span class="brand__dot"></span>KORV PTY LTD</div>
  </section>
</body>
</html>
```